Custom unique Stationary design for Logistics company

We need a custom, unique , elegant and luxurious full stationary design using our new logo, following these guidelines:
1- Business card: double sided, both sides uses the navy blue as the background main color (same as the code of the navy blue used in our logo).
2- envelope and folder: also use the same navy blue as the main background color.
3- book cover( notepad cover) : same thing with the navy blue
4- letterhead: feel free to use the combination of the colors in our logo.
5- rest of the items are up to your creativity

Target Market(s)

corporates and other businesses

Industry/Entity Type

Logistics and heavy machines contractors

Requirements
Must have
• Letterhead, business card, envelope, notepad cover, paper, file
Nice to have
• navy blue to be main background color for business card, envelope, notepad cover

```html
<!DOCTYPE html>
<html lang="en">
<head>
<meta charset="utf-8">
<title>Keystone Transit Company – Notebook Covers</title>
<link rel="stylesheet" href="https://fonts.googleapis.com/css2?family=Montserrat:wght@800&family=Open+Sans:wght@700&display=swap">
<style>
  :root {
    --page-bg: #8cc3e3;
    --navy: #064a70;
    --navy-deep: #034066;
    --navy-light: #17759f;
    --spine: #1f4e6b;
    --orange: #f26a3a;
    --orange-light: #f6895a;
    --white: #ffffff;
    --photo-sky: #d8e8f4;
    --photo-steel: #4e6f94;
    --photo-dark: #2c3f5c;
  }
  * { margin: 0; padding: 0; box-sizing: border-box; }
  html, body { width: 1200px; height: 900px; overflow: hidden; }
  body { background: var(--page-bg); position: relative; }

  .cover {
    position: absolute;
    top: 36px;
    width: 505px;
    height: 785px;
    border-radius: 0 26px 26px 0;
    overflow: hidden;
    background: var(--navy);
  }
  .cover--front { left: 64px; }
  .cover--back {
    left: 641px;
    background: linear-gradient(180deg, var(--navy-light) 0%, var(--navy) 45%, var(--navy-deep) 100%);
  }
  .cover__spine {
    position: absolute; left: 0; top: 0; bottom: 0; width: 20px;
    background: var(--spine);
    z-index: 3;
  }
  .cover__art { position: absolute; left: 0; top: 0; width: 505px; height: 320px; }

  .cover__brand {
    position: absolute; left: 20px; right: 0;
    display: flex; align-items: center; justify-content: center; gap: 16px;
    font-family: "Montserrat", sans-serif; font-weight: 800;
    color: var(--white);
    letter-spacing: 1px;
  }
  .cover--front .cover__brand { top: 500px; font-size: 62px; }
  .cover--back .cover__brand { top: 660px; font-size: 30px; gap: 9px; }
  .brand-dot { border-radius: 50%; background: var(--orange); flex: none; }
  .cover--front .brand-dot { width: 26px; height: 26px; }
  .cover--back .brand-dot { width: 13px; height: 13px; }

  .cover__tagline {
    position: absolute; left: 20px; right: 0; top: 586px;
    text-align: center;
    font-family: "Montserrat", sans-serif; font-weight: 800;
    font-size: 15px; letter-spacing: 1px;
    color: #9fb4c4;
  }

  .cover__band {
    position: absolute; left: 0; right: 0; bottom: 0; height: 44px;
    background: linear-gradient(180deg, var(--orange-light), var(--orange));
    display: flex; align-items: center; justify-content: center;
    padding-left: 20px;
  }
  .cover__url {
    font-family: "Open Sans", sans-serif; font-weight: 700;
    font-size: 16px; color: var(--white);
  }
</style>
</head>
<body>

  <section class="cover cover--front" aria-label="Notebook front cover">
    <div class="cover__spine"></div>
    <svg class="cover__art" viewBox="0 0 505 320" width="505" height="320">
      <defs>
        <linearGradient id="photoTone" x1="0" y1="0" x2="1" y2="1">
          <stop offset="0" stop-color="var(--photo-sky)"/>
          <stop offset="0.45" stop-color="var(--photo-steel)"/>
          <stop offset="1" stop-color="var(--photo-dark)"/>
        </linearGradient>
        <linearGradient id="swoosh" x1="0" y1="0" x2="1" y2="0">
          <stop offset="0" stop-color="#ffffff"/>
          <stop offset="1" stop-color="#c9d3dc"/>
        </linearGradient>
      </defs>
      <g role="img" aria-label="Photograph of a cargo ship, port cranes, aircraft and trucks linked by a network of logistics icons">
        <rect x="0" y="0" width="505" height="300" fill="url(#photoTone)"/>
      </g>
      <path d="M0 280 Q 200 220 505 300 L505 320 L0 320 Z" fill="url(#swoosh)"/>
      <path d="M0 292 Q 210 240 505 320 L0 320 Z" fill="var(--navy-light)"/>
      <path d="M0 300 Q 215 255 505 330 L505 320 L0 320 Z" fill="var(--navy)"/>
    </svg>
    <div class="cover__brand"><span class="brand-dot"></span>KEYSTONE</div>
    <div class="cover__tagline">KEYSTONE TRANSIT COMPANY</div>
    <div class="cover__band"><span class="cover__url">www.keystonetransit.com</span></div>
  </section>

  <section class="cover cover--back" aria-label="Notebook back cover">
    <div class="cover__spine"></div>
    <div class="cover__brand"><span class="brand-dot"></span>KEYSTONE</div>
    <div class="cover__band"></div>
  </section>

</body>
</html>
```